We are a doctors medical practice
I need the business card to be eye catching and memorable,
to reflect professionalism, yet also warmth and care

the numbers need to be easy to see, for the elderly

and the logo also in a location that is large enough to see and be eye catching

Back of card:
opening hours:
Mon- Fri 8.30am to 6pm
Sat 9am to 4pm

rows for appontments, date and time
Updates

HiĀ 

Modification to company name

BROOKVALE KINDRED HEALTH MEDICAL PRACTICE

Thanks
Marla

Reason: I am look for a unique design that also fulfils the design brief

I have attempted to post a .eps and .ai file of the logo

Target Market(s)

needs to appeal to the majority, mainly adults

Industry/Entity Type

Medical

Contact Information for Business Card

company name: Brookvale Kindred Health Medical Practice
Name: Dr Marla Tobrik-Vey
Qualifications: MBBS, Bsci(med), FRACGP, DCH, SH&FPA, Dip Derm
Address: Shop 3/41-43 Corrow St, Fairfield 2165
Ph: 02 9184 3025
Fax: 02 9318 6042

Requirements
Nice to have
• I like balance
gold/ silver incorporated, as well as the other colours in the logo- but not limited to these colours
a "medical" feel
Should not have
• dark or strong colours

```html
<!DOCTYPE html>
<html lang="en">
<head>
<meta charset="utf-8">
<title>Brookvale Kindred Health Medical Practice – Business Card</title>
<link href="https://fonts.googleapis.com/css2?family=Open+Sans:wght@400;600;700&display=swap" rel="stylesheet">
<style>
  :root {
    --page-bg: #eef1f4;
    --card-white: #ffffff;
    --brand-blue: #1a95d6;
    --blue-soft: #5cb8e6;
    --navy: #1d3f73;
    --accent-yellow: #f6ec1c;
    --text-white: #ffffff;
    --ink: #2b2b2b;
    --grey-top: #ffffff;
    --grey-bottom: #d4d4d4;
  }
  * { box-sizing: border-box; margin: 0; padding: 0; }
  html, body {
    width: 1200px; height: 900px; overflow: hidden;
    background: var(--page-bg);
    font-family: "Open Sans", Arial, sans-serif;
  }
  .canvas {
    width: 1200px; height: 900px;
    display: flex; flex-direction: column; align-items: center; justify-content: center;
    gap: 36px;
  }
  .card {
    width: 700px; height: 400px; position: relative; overflow: hidden;
    box-shadow: 0 6px 18px rgba(0,0,0,.18);
  }

  /* Front */
  .card-front { background: var(--brand-blue); }
  .front-header {
    height: 92px; background: var(--card-white);
    display: flex; align-items: center; gap: 16px; padding-left: 28px;
  }
  .brand-dot {
    width: 58px; height: 58px; border-radius: 50%;
    border: 4px solid var(--brand-blue); flex: none;
  }
  .practice-name {
    color: var(--navy); font-weight: 600; font-size: 21px; letter-spacing: .3px;
  }
  .front-emblem {
    position: absolute; left: 40px; top: 130px;
    width: 250px; height: 250px; border-radius: 50%;
    background: radial-gradient(circle at 45% 45%, #7ccaef 0%, var(--blue-soft) 70%);
    opacity: .85;
  }
  .front-details {
    position: absolute; left: 318px; top: 112px; right: 20px; color: var(--text-white);
  }
  .doctor-name {
    color: var(--accent-yellow); font-weight: 700; font-size: 31px; line-height: 1.1;
  }
  .qualifications {
    font-size: 15px; font-weight: 600; line-height: 1.35; margin-top: 6px;
  }
  .contact-table {
    margin-top: 34px; border-collapse: collapse; font-size: 19px; line-height: 1.35;
  }
  .contact-table td { vertical-align: top; padding: 0; }
  .contact-label { width: 92px; }
  .contact-sep { width: 20px; }

  /* Back */
  .card-back {
    background: linear-gradient(to bottom, var(--grey-top) 25%, var(--grey-bottom) 100%);
  }
  .hours-band {
    height: 118px; background: var(--brand-blue);
    display: flex; align-items: center; padding-left: 34px; gap: 22px;
    color: var(--accent-yellow);
  }
  .hours-title { font-size: 30px; font-weight: 600; }
  .hours-list { font-size: 26px; font-weight: 600; line-height: 1.2; }
  .hours-list .sat { padding-left: 24px; }
  .appointments {
    position: absolute; left: 34px; right: 34px; top: 134px;
  }
  .appointments-head {
    display: flex; justify-content: space-between;
    font-size: 16px; font-weight: 600; color: var(--ink);
  }
  .appointment-row {
    height: 29px; border-bottom: 2px dotted var(--ink);
  }
</style>
</head>
<body>
<main class="canvas">

  <section class="card card-front" aria-label="Business card front">
    <header class="front-header">
      <span class="brand-dot" aria-hidden="true"></span>
      <h1 class="practice-name">BROOKVALE KINDRED HEALTH MEDICAL PRACTICE</h1>
    </header>
    <div class="front-emblem" role="img" aria-label="Large soft-blue emblem area of the practice"></div>
    <div class="front-details">
      <h2 class="doctor-name">Dr Marla Tobrik-Vey</h2>
      <p class="qualifications">MBBS, Bsci(med), FRACGP,<br>DCH, SH&amp;FPA, Dip Derm</p>
      <table class="contact-table">
        <tr><td class="contact-label">Tel</td><td class="contact-sep">:</td><td>02 9184 3025</td></tr>
        <tr><td class="contact-label">Fax</td><td class="contact-sep">:</td><td>02 9318 6042</td></tr>
        <tr><td class="contact-label">Address</td><td class="contact-sep">:</td><td>Shop 3/41-43 Corrow St,<br>Kindrewood 2199</td></tr>
      </table>
    </div>
  </section>

  <section class="card card-back" aria-label="Business card back">
    <div class="hours-band">
      <span class="hours-title">OPENING HOURS:</span>
      <div class="hours-list">
        <div>Mon- Fri 8.30am to 6pm</div>
        <div class="sat">Sat 9am to 4pm</div>
      </div>
    </div>
    <div class="appointments">
      <div class="appointments-head">
        <span>Appontments</span>
        <span>Date &amp; Time</span>
      </div>
      <div class="appointment-row"></div>
      <div class="appointment-row"></div>
      <div class="appointment-row"></div>
      <div class="appointment-row"></div>
      <div class="appointment-row"></div>
      <div class="appointment-row"></div>
      <div class="appointment-row"></div>
      <div class="appointment-row"></div>
    </div>
  </section>

</main>
</body>
</html>
```